Modern Attractive Letterhead for Veterinary House Call Business.

A letterhead which can be printed on A4, A5 and A6 paper sizes.
To have: ( our files to be uploaded)
1. Logo with Text
2. telephone
3. email
4. website
5. Address

Target Market(s)

60-85year mainly women pet owners. Also market include families, young professionals, busy people who have dogs and cats

Industry/Entity Type

Business

Requirements
Must have
• 1. Logo with Text ( provided)
• 2. telephone
• 3. email
• 4. website
• 5. Address
Nice to have
• Needs to be modern, preferably warm and caring in nature( if possible )
Should not have
• difficulty in printing A5 and A6

```html
<!DOCTYPE html>
<html lang="en">
<head>
<meta charset="utf-8">
<title>Hearthside Pet Care Letterhead</title>
<link href="https://fonts.googleapis.com/css2?family=Open+Sans:wght@400;600&display=swap" rel="stylesheet">
<style>
  :root {
    --paper: #ffffff;
    --brand-blue: #1f5fae;
    --rule-green: #2e8b3a;
    --band-navy: #222f72;
    --band-bright: #2a9ad8;
    --band-text: #ffffff;
  }
  html, body {
    margin: 0;
    padding: 0;
    overflow: hidden;
    background: #f2f2f2;
  }
  .letterhead {
    position: relative;
    width: 948px;
    height: 1200px;
    background: var(--paper);
    overflow: hidden;
    font-family: "Open Sans", Arial, sans-serif;
  }
  .brand {
    position: absolute;
    top: 70px;
    left: 0;
    right: 0;
    display: flex;
    justify-content: center;
    align-items: center;
    gap: 16px;
  }
  .brand-dot {
    width: 38px;
    height: 38px;
    border-radius: 50%;
    background: var(--brand-blue);
  }
  .brand-name {
    font-size: 40px;
    font-weight: 600;
    color: var(--brand-blue);
    letter-spacing: 0.5px;
  }
  .footer-rule {
    position: absolute;
    left: 0;
    right: 0;
    top: 1150px;
    height: 3px;
    background: var(--rule-green);
  }
  .contact-band {
    position: absolute;
    left: 0;
    right: 0;
    top: 1160px;
    height: 40px;
    background: linear-gradient(90deg, var(--band-navy) 0%, #2b5fa8 35%, var(--band-bright) 52%, #2b5fa8 68%, var(--band-navy) 100%);
    display: flex;
    justify-content: center;
    align-items: center;
    gap: 14px;
    color: var(--band-text);
    font-size: 15px;
  }
  .contact-item {
    display: flex;
    align-items: center;
    gap: 6px;
  }
  .contact-item svg {
    width: 13px;
    height: 13px;
  }
  .divider {
    width: 1px;
    height: 18px;
    background: rgba(255,255,255,0.6);
  }
</style>
</head>
<body>
  <main class="letterhead">
    <header class="brand">
      <span class="brand-dot"></span>
      <span class="brand-name">Hearthside Pet Care</span>
    </header>

    <div class="footer-rule"></div>
    <footer class="contact-band">
      <span class="contact-item">
        <svg viewBox="0 0 16 16" aria-hidden="true"><path d="M3.5 1.5l2.5 3-1.5 1.5c.8 1.8 2.2 3.2 4 4l1.5-1.5 3 2.5-1.5 2.5C7 13 3 9 1 4z" fill="none" stroke="#fff" stroke-width="1.4" stroke-linejoin="round"/></svg>
        0400 555 218
      </span>
      <span class="contact-item">
        <svg viewBox="0 0 16 16" aria-hidden="true"><rect x="1" y="3.5" width="14" height="9" rx="1" fill="#fff"/><path d="M1.5 4l6.5 5 6.5-5" fill="none" stroke="#2b5fa8" stroke-width="1.3"/></svg>
        hello@hearthsidepetcare.com.au
      </span>
      <span class="contact-item">
        <svg viewBox="0 0 16 16" aria-hidden="true"><g fill="none" stroke="#fff" stroke-width="1.3"><circle cx="8" cy="8" r="6.5"/><ellipse cx="8" cy="8" rx="3" ry="6.5"/><path d="M1.5 8h13M2.5 4.8h11M2.5 11.2h11"/></g></svg>
        www.hearthsidepetcare.com.au
      </span>
      <span class="divider"></span>
      <span class="contact-item">PO Box 3842 Riverbend QLD 4075</span>
    </footer>
  </main>
</body>
</html>
```